Brindle Sky Port needs a new upscale business card design for our high end aircraft hangar complex

Brindle Sky Port (BSP) is a large, upscale jet hangar complex in the US housing expensive aircraft. We need a new business card design, using our current logo. We will be attending a industry convention and need a card design that will stand out and be remembered by aircraft owners and private pilots.

Target Market(s)

Aircraft pilots or owners looking for a new upscale hangar

Industry/Entity Type

Airport

Contact Information for Business Card

I like to use very heavy card stock, 400#, double sided. Square, no rounded edges please.

Colors
3276b5
0255a3
85abd2

Requirements
Must have
• An expensive, classy design, vivid colors.
Nice to have
• Needs to look very expensive and classy, and have some "pop". Designer must be able to download or copy my current typeface or fonts.
• One card side might be black with the "Logo and Brindle Sky Port Double line image in blue (or try gold, or glossy black), and perhaps have a grayed out "K720 jet silhouette". The other card side would have our contact info, and perhaps the "BSP Logo only". I'd like my contact info 'stacked', not in a paragraph format.
Should not have
• Should not look "too busy". Having a double-sided card will help.

```html
<!DOCTYPE html>
<html lang="en">
<head>
<meta charset="utf-8">
<title>Brindle Sky Port – Business Card</title>
<link href="https://fonts.googleapis.com/css2?family=Arimo:wght@400;700&display=swap" rel="stylesheet">
<style>
  :root {
    --backdrop: #8c8d8f;
    --card: #0d0d0e;
    --brand-blue: #2f6aa6;
    --band-bright: #0255a3;
    --band-dark: #0a2646;
    --text-light: #e8e8e8;
    --divider: #9a9a9a;
  }
  * { margin: 0; padding: 0; box-sizing: border-box; }
  html, body {
    width: 1105px; height: 1200px; overflow: hidden;
    background: var(--backdrop);
    font-family: "Arimo", Arial, sans-serif;
  }
  .card {
    position: absolute; left: 182px; width: 747px; height: 427px;
    background: var(--card); overflow: hidden;
  }
  .card--front { top: 119px; }
  .card--back { top: 635px; }
  .card__bands { position: absolute; inset: 0; width: 100%; height: 100%; }

  .brand {
    position: absolute; text-align: center;
    color: var(--brand-blue); font-weight: 700; line-height: 1;
  }
  .brand__mark { display: block; font-size: 78px; letter-spacing: 4px; }
  .brand__name { display: block; font-size: 27px; margin-top: 8px; letter-spacing: 1px; }
  .card--front .brand { left: 60px; top: 125px; width: 330px; }
  .card--back .brand { left: 209px; top: 150px; width: 330px; }

  .divider {
    position: absolute; left: 394px; top: 61px; width: 1px; height: 311px;
    background: linear-gradient(to bottom, transparent, var(--divider) 20%, var(--divider) 80%, transparent);
  }
  .contact { position: absolute; left: 421px; top: 76px; color: var(--text-light); }
  .contact__name { color: var(--brand-blue); font-size: 26px; font-weight: 400; }
  .contact__title { font-size: 20px; margin-top: 6px; }
  .contact__address { font-size: 18px; line-height: 25px; margin-top: 13px; }
  .contact__list { list-style: none; margin-top: 12px; }
  .contact__item {
    display: flex; align-items: center; font-size: 18px; height: 28.5px;
  }
  .contact__icon { width: 18px; height: 18px; margin-right: 17px; fill: var(--brand-blue); flex: none; }

  .website {
    position: absolute; left: 0; right: 0; top: 359px; text-align: center;
    color: var(--text-light); font-size: 18px; letter-spacing: 3.5px;
  }
</style>
</head>
<body>

<section class="card card--front">
  <svg class="card__bands" viewBox="0 0 747 427" aria-hidden="true">
    <defs>
      <linearGradient id="bandTop" x1="0" x2="1" y1="0" y2="0">
        <stop offset="0" stop-color="var(--band-bright)"/>
        <stop offset="1" stop-color="var(--band-dark)"/>
      </linearGradient>
      <linearGradient id="bandBottom" x1="0" x2="1" y1="0" y2="0">
        <stop offset="0" stop-color="var(--band-dark)"/>
        <stop offset="1" stop-color="var(--band-bright)"/>
      </linearGradient>
    </defs>
    <polygon points="0,0 747,0 747,3 0,47" fill="url(#bandTop)"/>
    <polygon points="50,427 747,374 747,427" fill="url(#bandBottom)"/>
  </svg>

  <div class="brand">
    <span class="brand__mark">BSP</span>
    <span class="brand__name">Brindle Sky Port</span>
  </div>

  <div class="divider"></div>

  <div class="contact">
    <h1 class="contact__name">Evan Marlow</h1>
    <p class="contact__title">President</p>
    <p class="contact__address">2170 Harrow Lane<br>Cedar Bluff, NY 11940</p>
    <ul class="contact__list">
      <li class="contact__item">
        <svg class="contact__icon" viewBox="0 0 20 20" aria-hidden="true"><path d="M2 6c0-2 3-3 8-3s8 1 8 3v2h-4V6H6v2H2zM5 9h10l2 8H3z"/></svg>
        555 0142 2290
      </li>
      <li class="contact__item">
        <svg class="contact__icon" viewBox="0 0 20 20" aria-hidden="true"><path d="M6 1h8a1 1 0 0 1 1 1v16a1 1 0 0 1-1 1H6a1 1 0 0 1-1-1V2a1 1 0 0 1 1-1zm1 2v12h6V3z"/></svg>
        555 0187 4416
      </li>
      <li class="contact__item">
        <svg class="contact__icon" viewBox="0 0 20 20" aria-hidden="true"><path d="M5 1h10v5H5zM2 7h16v8h-3v4H5v-4H2zm5 6v4h6v-4z"/></svg>
        555 0163 7731
      </li>
      <li class="contact__item">
        <svg class="contact__icon" viewBox="0 0 20 20" aria-hidden="true"><path d="M2 4h16v12H2zm1.5 1.5L10 11l6.5-5.5z"/></svg>
        evan@brindlesky.com
      </li>
      <li class="contact__item">
        <svg class="contact__icon" viewBox="0 0 20 20" aria-hidden="true"><circle cx="10" cy="10" r="9"/></svg>
        www.brindleskyport.com
      </li>
    </ul>
  </div>
</section>

<section class="card card--back">
  <div class="brand">
    <span class="brand__mark">BSP</span>
    <span class="brand__name">Brindle Sky Port</span>
  </div>
  <p class="website">www.brindleskyport.com</p>
</section>

</body>
</html>
```